Creative, fresh business card design for Ripplecraft Facades

We need a fresh, creative business card design for Ripplecraft Facades. We are the manufacturer of Ripplecraft Facades in Australia. Wall panels are 2400 x 1200mm panels made from MDF and feature 3D patterns on the face of the panel. The colours to be used are green, silver/grey and white RGB
Red 187
Green 207
Blue 65.

An idea is to possibly use a watermark of one of our designs as a background (like on the "Grids" design on the left hand side of page 2 of our brochure).

Target Market(s)

Interior designers, architects, builders and home renovators

Industry/Entity Type

Business

Contact Information for Business Card

Details to go on the card are:
Our logo (attached),
Slogan: "Decorative panels for interiors and exteriors",
Contact name,
Position,
Mobile phone number,
Business address,
Business phone,
Business fax,
Website and
Email address.

I have attached a few images of our panels and our brochure for reference.

The colours of the business card should feature our logo colours which are: RGB
Red 187
Green 207
Blue 65

Requirements
Must have
• Very modern fonts and design. Some of the designs shown especially the "Prisms" design which is a popular design.
Nice to have
• Creative but simple design. Very contemporary.
Should not have
• Anything ornate or old fashioned.

```html
<!DOCTYPE html>
<html lang="en">
<head>
<meta charset="utf-8">
<title>Ripplecraft Facades – Business Cards</title>
<link href="https://fonts.googleapis.com/css2?family=Arimo:wght@400;700&display=swap" rel="stylesheet">
<style>
  :root {
    --brand-green: rgb(187, 207, 65);
    --panel-grey: #8a8b8e;
    --slogan-grey: #9a9b9e;
    --card-white: #ffffff;
    --backdrop: #e9e9ea;
    --photo-dark: #4a4b4d;
    --photo-mid: #8c8d8f;
    --photo-light: #c9c3b8;
  }
  html, body {
    margin: 0;
    width: 1200px;
    height: 1200px;
    overflow: hidden;
    background: var(--backdrop);
    font-family: "Arimo", Arial, sans-serif;
  }
  .sheet {
    position: relative;
    width: 1240px;
    height: 1240px;
    transform: scale(0.9677);
    transform-origin: 0 0;
  }
  .card {
    position: absolute;
    width: 530px;
    height: 305px;
    background: var(--card-white);
    box-shadow: 0 2px 6px rgba(0,0,0,0.15);
  }
  .col-left { left: 75px; }
  .col-right { left: 636px; }
  .row-1 { top: 130px; }
  .row-2 { top: 466px; }
  .row-3 { top: 802px; }

  .person {
    position: absolute;
    left: 22px; top: 21px;
    width: 181px; height: 128px;
    background: var(--panel-grey);
    color: var(--card-white);
    box-sizing: border-box;
    padding: 31px 0 0 18px;
    font-size: 14px;
    line-height: 17px;
  }
  .person-name { font-weight: 700; margin: 0; }
  .person-role { margin: 0 0 17px; }
  .person-mobile { margin: 0; }
  .person-mobile b { font-weight: 700; }

  .panel-photo {
    position: absolute;
    left: 207px; top: 21px;
    width: 299px; height: 128px;
    background: linear-gradient(90deg, var(--photo-dark) 0%, var(--photo-mid) 55%, var(--photo-dark) 82%, var(--photo-light) 84%, var(--photo-light) 100%);
  }

  .slogan {
    position: absolute;
    left: 22px; top: 154px;
    width: 484px;
    margin: 0;
    font-size: 16px;
    letter-spacing: 3.1px;
    color: var(--slogan-grey);
    white-space: nowrap;
  }

  .brand-block {
    position: absolute;
    left: 22px; top: 179px;
    width: 181px; height: 105px;
    background: var(--brand-green);
    display: flex;
    align-items: center;
    justify-content: center;
    text-align: center;
  }
  .brand-name {
    margin: 0;
    color: var(--card-white);
    font-weight: 700;
    font-size: 24px;
    line-height: 27px;
  }

  .contact {
    position: absolute;
    left: 208px; top: 179px;
    width: 300px; height: 105px;
    background: var(--brand-green);
    color: var(--card-white);
    box-sizing: border-box;
    padding: 17px 0 0 17px;
    font-size: 13px;
    line-height: 17.6px;
  }
  .contact p { margin: 0; white-space: nowrap; }
  .contact b { font-weight: 700; }
</style>
</head>
<body>
<main class="sheet">

  <article class="card col-left row-1">
    <div class="person">
      <p class="person-name">Hanna Lindqvist</p>
      <p class="person-role">Director</p>
      <p class="person-mobile">M <b>0400 123 401</b></p>
    </div>
    <div class="panel-photo" role="img" aria-label="Photo of a rippled 3D wall panel in an interior"></div>
    <p class="slogan">decorative panels for interiors &amp; exteriors</p>
    <div class="brand-block"><p class="brand-name">Ripplecraft<br>Facades</p></div>
    <div class="contact">
      <p>P <b>02 9000 1100</b>&nbsp; F <b>02 9000 1199</b></p>
      <p>12 Sample Street, Westfield Vale NSW 2000</p>
      <p>hanna@ripplecraft.com.au</p>
      <p><b>www.ripplecraft.com.au</b></p>
    </div>
  </article>

  <article class="card col-right row-1">
    <div class="person">
      <p class="person-name">Oskar Lindqvist</p>
      <p class="person-role">Director</p>
      <p class="person-mobile">M <b>0400 123 402</b></p>
    </div>
    <div class="panel-photo" role="img" aria-label="Photo of a rippled 3D wall panel in an interior"></div>
    <p class="slogan">decorative panels for interiors &amp; exteriors</p>
    <div class="brand-block"><p class="brand-name">Ripplecraft<br>Facades</p></div>
    <div class="contact">
      <p>P <b>02 9000 1100</b>&nbsp; F <b>02 9000 1199</b></p>
      <p>12 Sample Street, Westfield Vale NSW 2000</p>
      <p>oskar@ripplecraft.com.au</p>
      <p><b>www.ripplecraft.com.au</b></p>
    </div>
  </article>

  <article class="card col-left row-2">
    <div class="person">
      <p class="person-name">Tobias Lindqvist</p>
      <p class="person-role">General Manager</p>
      <p class="person-mobile">M <b>0400 123 403</b></p>
    </div>
    <div class="panel-photo" role="img" aria-label="Photo of a rippled 3D wall panel in an interior"></div>
    <p class="slogan">decorative panels for interiors &amp; exteriors</p>
    <div class="brand-block"><p class="brand-name">Ripplecraft<br>Facades</p></div>
    <div class="contact">
      <p>P <b>02 9000 1100</b>&nbsp; F <b>02 9000 1199</b></p>
      <p>12 Sample Street, Westfield Vale NSW 2000</p>
      <p>tobias@ripplecraft.com.au</p>
      <p><b>www.ripplecraft.com.au</b></p>
    </div>
  </article>

  <article class="card col-right row-2">
    <div class="person">
      <p class="person-name">Dean Marsh</p>
      <p class="person-role">Production Manager</p>
      <p class="person-mobile">M <b>0400 123 404</b></p>
    </div>
    <div class="panel-photo" role="img" aria-label="Photo of a rippled 3D wall panel in an interior"></div>
    <p class="slogan">decorative panels for interiors &amp; exteriors</p>
    <div class="brand-block"><p class="brand-name">Ripplecraft<br>Facades</p></div>
    <div class="contact">
      <p>P <b>02 9000 1100</b>&nbsp; F <b>02 9000 1199</b></p>
      <p>12 Sample Street, Westfield Vale NSW 2000</p>
      <p>sales@ripplecraft.com.au</p>
      <p><b>www.ripplecraft.com.au</b></p>
    </div>
  </article>

  <article class="card col-left row-3">
    <div class="person">
      <p class="person-name">Carla Benton</p>
      <p class="person-role">Office administrator</p>
      <p class="person-mobile">M <b>0400 123 405</b></p>
    </div>
    <div class="panel-photo" role="img" aria-label="Photo of a rippled 3D wall panel in an interior"></div>
    <p class="slogan">decorative panels for interiors &amp; exteriors</p>
    <div class="brand-block"><p class="brand-name">Ripplecraft<br>Facades</p></div>
    <div class="contact">
      <p>P <b>02 9000 1100</b>&nbsp; F <b>02 9000 1199</b></p>
      <p>12 Sample Street, Westfield Vale NSW 2000</p>
      <p>sales@ripplecraft.com.au</p>
      <p><b>www.ripplecraft.com.au</b></p>
    </div>
  </article>

  <article class="card col-right row-3">
    <div class="person">
      <p class="person-name">Mira Kostas</p>
      <p class="person-role">Office administrator</p>
      <p class="person-mobile">M <b>0400 123 406</b></p>
    </div>
    <div class="panel-photo" role="img" aria-label="Photo of a rippled 3D wall panel in an interior"></div>
    <p class="slogan">decorative panels for interiors &amp; exteriors</p>
    <div class="brand-block"><p class="brand-name">Ripplecraft<br>Facades</p></div>
    <div class="contact">
      <p>P <b>02 9000 1100</b>&nbsp; F <b>02 9000 1199</b></p>
      <p>12 Sample Street, Westfield Vale NSW 2000</p>
      <p>sales@ripplecraft.com.au</p>
      <p><b>www.ripplecraft.com.au</b></p>
    </div>
  </article>

</main>
</body>
</html>
```